Corvane Systems Web Site

Need a complete redesign of the website to make it cleaner and up to date.
Current website: http://www.corvanesystems.example/
I am looking for a single page design focused on giving all the information about the POC (Pump Off Controller). And highlighting its benefits: Increased oil production, quick ROI, ease of use and low maintenance cost.
Here's a presentation of the product:
http://slidewharf.example/qk4mtz8vn2ra/?utm_campaign=share&utm_medium=copy&rc=ex0share
Please consider participating on the flyer design:
http://jobs.artmarket.example/job.aspx?id=391726
Here are some design examples of web sites I like:
http://www.bright-harbor.example/
I just added the source files for our business cards. I would like to see designs that incorporate the "tag cloud" on the back of the card..
Target Market(s)
Oil field decision makers. Engineers and technicians from 20 to 60.
Investors and venture capitalists.
Industry/Entity Type
Cleaner
Requirements
Must have
- Single page design
Nice to have
- Responsive web design

```html
<!DOCTYPE html>
<html lang="en">
<head>
<meta charset="utf-8">
<title>Corvane Systems – Pump Off Controllers</title>
<link rel="stylesheet" href="https://fonts.googleapis.com/css2?family=Oswald:wght@400;500;600&family=Open+Sans:wght@400;600;700&display=swap">
<style>
:root{
  --red:#e1261c;
  --red-dark:#b81b13;
  --navy:#1f2a5c;
  --blue:#2f3d8f;
  --ink:#2a2a2a;
  --muted:#6b6b6b;
  --line:#e2e2e2;
  --soft:#f3f3f3;
  --footer:#2b2b2b;
  --footer-deep:#1e1e1e;
  --white:#ffffff;
}
*{box-sizing:border-box;margin:0;padding:0}
html,body{width:771px;height:1200px;overflow:hidden}
body{font-family:"Open Sans",Arial,sans-serif;color:var(--ink);background:var(--white);font-size:9px;line-height:1.5}
.heading{font-family:"Oswald",Arial,sans-serif;text-transform:uppercase;color:var(--navy);font-weight:500;font-size:17px;letter-spacing:.3px}
.btn{display:inline-block;background:var(--red);color:var(--white);font-family:"Oswald",Arial,sans-serif;font-size:8px;letter-spacing:.5px;padding:4px 9px;text-transform:uppercase}

/* header */
.topbar{height:48px;position:relative;padding:0 30px;display:flex;align-items:center;justify-content:space-between}
.brand{display:flex;align-items:center;gap:7px;font-family:"Oswald",Arial,sans-serif;font-weight:600;font-size:19px;color:var(--red);letter-spacing:1px;text-transform:uppercase}
.brand-mark{width:16px;height:16px;border-radius:50%;background:var(--red)}
.contact-strip{display:flex;align-items:center;gap:16px;font-size:8.5px;color:var(--muted)}
.contact-strip span{display:flex;align-items:center;gap:4px}
.login{background:var(--red);color:var(--white);font-family:"Oswald",Arial,sans-serif;font-size:9px;padding:5px 14px;display:flex;align-items:center;gap:5px}
.nav{height:28px;background:var(--navy);display:flex;justify-content:flex-end;padding-right:30px}
.nav a{color:var(--white);text-decoration:none;font-family:"Oswald",Arial,sans-serif;font-size:9.5px;letter-spacing:.6px;padding:0 18px;display:flex;align-items:center}
.nav a.active{background:var(--red)}

/* hero */
.hero{height:226px;position:relative;background:linear-gradient(180deg,#9fb4cc 0%,#c9d5df 55%,#7d7466 80%,#5a5247 100%)}
.hero-copy{position:absolute;right:40px;top:62px;width:300px;background:rgba(20,24,40,.72);padding:12px 16px;font-family:"Oswald",Arial,sans-serif;color:var(--white);font-size:17px;line-height:1.25;font-weight:500}

/* about + video */
.about{height:310px;display:flex;gap:30px;padding:26px 56px 0}
.about-text{flex:1}
.about-text .underline,.video .underline{height:2px;background:var(--line);margin:6px 0 12px;position:relative}
.underline::before{content:"";position:absolute;left:0;top:0;width:40px;height:2px;background:var(--red)}
.lead{font-weight:700;font-size:9.5px;margin-bottom:8px}
.about-text p{color:var(--muted);margin-bottom:10px}
.video{width:310px}
.video-frame{height:196px;position:relative;background:linear-gradient(180deg,#b9c6d3 0%,#d8dde0 55%,#6b6256 100%)}
.video-controls{position:absolute;left:0;right:0;bottom:0;height:18px;background:rgba(0,0,0,.75);display:flex;align-items:center;gap:8px;padding:0 8px}
.progress{flex:1;height:3px;background:#666;position:relative}
.progress::before{content:"";position:absolute;left:0;top:0;width:30%;height:3px;background:var(--red)}

/* features */
.features{height:200px;background:var(--blue);display:flex;gap:14px;padding:28px 56px}
.feature{flex:1;background:var(--white);padding:6px;text-align:center;display:flex;flex-direction:column;align-items:center}
.feature-photo{width:100%;height:66px;background:linear-gradient(180deg,#a9b9c9,#6f6a61)}
.feature h3{font-size:9px;font-weight:600;margin:8px 4px 6px;line-height:1.3;min-height:24px}

/* feedback */
.feedback{height:172px;padding-top:16px;text-align:center}
.feedback .heading{color:var(--blue)}
.quote{margin:12px 56px 0;border:1px solid var(--line);background:var(--soft);padding:14px 90px 12px 40px;position:relative;text-align:left;font-style:italic;color:var(--muted);height:90px}
.quote-mark{position:absolute;left:12px;top:4px;font-family:Georgia,serif;font-size:30px;color:#bbb;font-style:normal}
.avatar{position:absolute;right:18px;top:12px;width:54px;height:54px;border-radius:50%;background:linear-gradient(#d7dbe2,#aab1bd)}
.author{position:absolute;right:18px;bottom:8px;font-style:normal;font-size:8px;color:var(--ink)}

/* partners */
.partners{height:46px;background:var(--soft);display:flex;align-items:center;justify-content:space-between;padding:0 40px}
.partner{width:70px;height:16px;background:#cfcfcf;border-radius:3px}

/* footer */
.footer{height:130px;background:var(--footer);color:#cfcfcf;display:flex;gap:40px;padding:14px 40px 0}
.footer h4{font-family:"Oswald",Arial,sans-serif;color:var(--white);font-weight:500;font-size:11px;text-transform:uppercase;margin-bottom:8px}
.footer ul{list-style:none}
.footer li{font-size:8px;line-height:1.9}
.footer li::before{content:"› ";color:var(--red)}
.contact-list div{display:flex;gap:6px;font-size:8px;margin-bottom:6px}
.newsletter{margin-left:auto;width:230px;background:#3a3a3a;padding:10px 14px;margin-top:-4px;height:112px}
.newsletter p{font-size:8px;margin-bottom:6px}
.field{height:15px;background:var(--white);margin-bottom:5px;font-size:7.5px;color:#999;padding:2px 6px}
.copyright{height:25px;background:var(--footer-deep);color:#999;font-size:8px;text-align:center;line-height:25px}
</style>
</head>
<body>

<header class="topbar">
  <div class="brand"><span class="brand-mark"></span>Corvane</div>
  <div class="contact-strip">
    <span><svg width="8" height="8" viewBox="0 0 10 10"><path d="M2 1l2 2-1 1.5c.8 1.5 1.8 2.5 3.5 3.5L8 7l2 2-1.5 1C4.5 9.5.5 5.5 0 1.5z" fill="#e1261c"/></svg>(555) 014-2207</span>
    <span><svg width="9" height="7" viewBox="0 0 10 8"><rect x=".5" y=".5" width="9" height="7" fill="none" stroke="#e1261c"/><path d="M.5.5L5 4.5 9.5.5" fill="none" stroke="#e1261c"/></svg>info@corvanesystems.example</span>
    <a class="login"><svg width="7" height="8" viewBox="0 0 7 8"><rect x="0" y="3.5" width="7" height="4.5" fill="#fff"/><path d="M1.5 3.5V2a2 2 0 0 1 4 0v1.5" fill="none" stroke="#fff"/></svg>LOGIN</a>
  </div>
</header>

<nav class="nav">
  <a class="active">HOME</a><a>COMPANY</a><a>PRODUCTS</a><a>TELEMETRY</a><a>CONTACT US</a>
</nav>

<section class="hero" role="img" aria-label="Oil pumpjacks working in a field under a pale sky">
  <div class="hero-copy">Are Your Well Running Under A Timer Switch? Have You Thought Of Increasing The Barrel Count At Each Well? Corvane CAN Do It!</div>
</section>

<section class="about">
  <div class="about-text">
    <h2 class="heading">About Corvane</h2>
    <div class="underline"></div>
    <p class="lead">Corvane pump off controllers help operators cut energy use, reduce wear and raise daily barrel counts at every well site.</p>
    <p>Our controllers watch each stroke, stop the pump when fluid runs low and restart it at the right time. Field crews get clear alarms, simple setup and reports that show exactly where each well stands, so time is spent on the wells that need attention most.</p>
    <a class="btn">Read More</a>
  </div>
  <div class="video">
    <h2 class="heading">Our Video</h2>
    <div class="underline"></div>
    <div class="video-frame" role="img" aria-label="Video still of pumpjacks at an oil field">
      <div class="video-controls">
        <svg width="7" height="8" viewBox="0 0 7 8"><path d="M0 0l7 4-7 4z" fill="#fff"/></svg>
        <div class="progress"></div>
        <svg width="9" height="8" viewBox="0 0 9 8"><path d="M0 2.5h2L5 0v8L2 5.5H0z" fill="#fff"/></svg>
      </div>
    </div>
  </div>
</section>

<section class="features">
  <article class="feature"><div class="feature-photo" role="img" aria-label="Pumpjack at a well site"></div><h3>High Reliability and Accessibility</h3><a class="btn">Read More</a></article>
  <article class="feature"><div class="feature-photo" role="img" aria-label="Pumpjack at dusk"></div><h3>Alarm Generation and Reporting</h3><a class="btn">Read More</a></article>
  <article class="feature"><div class="feature-photo" role="img" aria-label="Row of pumpjacks in a field"></div><h3>Cost Savings due to Improved Pumper Efficiency</h3><a class="btn">Read More</a></article>
  <article class="feature"><div class="feature-photo" role="img" aria-label="Oil well equipment close up"></div><h3>Data Security</h3><a class="btn">Read More</a></article>
</section>

<section class="feedback">
  <h2 class="heading">Customer Feedback</h2>
  <blockquote class="quote">
    <span class="quote-mark">“</span>
    Since we installed the controllers our pumpers visit fewer wells each day, rod failures dropped and production went up within the first month. Setup was quick and support has been excellent throughout.
    <span class="avatar" role="img" aria-label="Customer portrait"></span>
    <span class="author">Daniel Okafor, USA</span>
  </blockquote>
</section>

<section class="partners" aria-label="Partners">
  <span class="partner"></span><span class="partner"></span><span class="partner"></span><span class="partner"></span><span class="partner"></span><span class="partner"></span><span class="partner"></span>
</section>

<footer class="footer">
  <div>
    <h4>Quick Links</h4>
    <ul><li>Home</li><li>Company</li><li>Products</li><li>Telemetry</li><li>Contact Us</li></ul>
  </div>
  <div class="contact-list">
    <h4>Contact Detail</h4>
    <div><svg width="8" height="10" viewBox="0 0 8 10"><path d="M4 0a4 4 0 0 1 4 4c0 3-4 6-4 6S0 7 0 4a4 4 0 0 1 4-4z" fill="#e1261c"/><circle cx="4" cy="4" r="1.4" fill="#2b2b2b"/></svg><span>4120 Meridian Way, Suite 210<br>Tulsa, OK 74103</span></div>
    <div><svg width="8" height="8" viewBox="0 0 10 10"><path d="M2 1l2 2-1 1.5c.8 1.5 1.8 2.5 3.5 3.5L8 7l2 2-1.5 1C4.5 9.5.5 5.5 0 1.5z" fill="#e1261c"/></svg><span>(555) 014-2207</span></div>
    <div><svg width="9" height="7" viewBox="0 0 10 8"><rect x=".5" y=".5" width="9" height="7" fill="none" stroke="#e1261c"/><path d="M.5.5L5 4.5 9.5.5" fill="none" stroke="#e1261c"/></svg><span>info@corvanesystems.example</span></div>
  </div>
  <div class="newsletter">
    <h4>Newsletter</h4>
    <p>Get Valuable Tips and News from Corvane. Signup to our Monthly Newsletter today!</p>
    <div class="field">Name</div>
    <div class="field">Email</div>
    <a class="btn">Subscribe</a>
  </div>
</footer>
<div class="copyright">Copyright © 2014 · CORVANE</div>

</body>
</html>
```